Business Card for Multi-Brand Sportswear Company

We are looking for a business card which represents our company and the multiple brands within it.

The company: Fen Athletics (LTD)
The brands: Fen, TavaPuni, ElmStretch, Grit and Rain

Employees using these cards would be representing Fen Athletics, rather than any of the individual brands. You will see a current design within the uploaded files, to give some inspiration. The actual text of the brands is not necessary, but the logos should be on there is some format.

Our creative minds on this are stretched, so we are looking for someone to make this their own, and show us what a good business card should look like.

We may like to get these printed with spot gloss, so keep that in mind with your designs.

www.fenathletics.co.uk

Industry/Entity Type

Business

Contact Information for Business Card

Leo Pemberton-Hale
Operations Manager
(+44) 1632 960 418
Leo@fenathletics.co.uk
www.fenathletics.co.uk

Font styles to use
Sans Serif
Other font styles liked:
• Eurostile

Colors
ffffff

Requirements
Nice to have
• Dark (black) background

```html
<!DOCTYPE html>
<html lang="en">
<head>
<meta charset="utf-8">
<title>Fen Athletics – Business Card</title>
<link rel="stylesheet" href="https://fonts.googleapis.com/css2?family=Michroma&family=Open+Sans:wght@400;600;700&display=swap">
<style>
  :root {
    --stage: #2b2725;
    --card-white: #ffffff;
    --card-black: #1c1c1c;
    --ink: #161616;
    --ink-soft: #6d6d6d;
    --accent-red: #e4211d;
    --text-light: #e9e9e9;
    --text-muted: #bdbdbd;
    --badge-purple: #5b4d6e;
    --badge-grey: #d9d9d9;
    --badge-pink: #f1d3d3;
  }
  * { box-sizing: border-box; margin: 0; padding: 0; }
  html, body { width: 1200px; height: 716px; overflow: hidden; }
  body {
    background: var(--stage);
    font-family: "Open Sans", Arial, sans-serif;
    position: relative;
  }
  .card {
    position: absolute;
    top: 208px;
    width: 520px;
    height: 300px;
    overflow: hidden;
  }
  .card--front { left: 50px; background: var(--card-white); }
  .card--back { left: 630px; background: var(--card-black); }

  .edge-band {
    position: absolute;
    left: 0; right: 0; bottom: 0;
    height: 12px;
    display: flex;
  }
  .edge-band__red { width: 52%; background: var(--accent-red); }
  .card--front .edge-band__rest { flex: 1; background: var(--ink); }
  .card--back .edge-band__rest { flex: 1; background: var(--card-white); }

  .brand-lockup {
    position: absolute;
    display: flex;
    flex-direction: column;
  }
  .card--front .brand-lockup { left: 120px; top: 78px; width: 280px; }
  .card--back .brand-lockup { left: 34px; top: 34px; width: 220px; }

  .wordmark {
    font-weight: 700;
    color: var(--ink);
    font-size: 34px;
    letter-spacing: 1px;
    line-height: 1;
    display: flex;
    align-items: center;
    gap: 10px;
  }
  .wordmark__square { width: 14px; height: 14px; background: var(--accent-red); }
  .card--back .wordmark { color: var(--text-light); font-size: 24px; }
  .card--back .wordmark__square { width: 10px; height: 10px; }

  .tagline {
    align-self: flex-end;
    font-size: 8px;
    font-weight: 700;
    letter-spacing: 1.5px;
    color: var(--ink);
    margin-top: 4px;
  }
  .card--back .tagline { color: var(--text-muted); font-size: 6px; }
  .rule { height: 2px; background: var(--ink-soft); margin-top: 5px; }

  .brand-row {
    display: flex;
    justify-content: space-between;
    margin-top: 14px;
  }
  .card--back .brand-row { margin-top: 10px; }
  .brand-badge {
    display: flex;
    flex-direction: column;
    align-items: center;
    gap: 4px;
  }
  .brand-badge__shape { width: 36px; height: 22px; border-radius: 3px; }
  .card--back .brand-badge__shape { width: 26px; height: 17px; }
  .brand-badge__name { font-size: 7px; font-weight: 600; color: var(--ink-soft); }
  .card--back .brand-badge__name { color: var(--text-muted); font-size: 6px; }
  .shape-purple { background: var(--badge-purple); }
  .shape-grey { background: var(--badge-grey); }
  .shape-pink { background: var(--badge-pink); }
  .shape-light { background: #ececec; }

  .company-line {
    font-family: "Michroma", "Open Sans", sans-serif;
    font-size: 12px;
    letter-spacing: 3px;
    color: var(--text-light);
    margin-top: 10px;
  }
  .person { position: absolute; left: 34px; top: 168px; }
  .person__name { font-size: 18px; font-weight: 600; color: var(--text-light); }
  .person__role { font-size: 11px; color: var(--text-muted); margin-top: 2px; margin-left: 40px; }

  .contact {
    position: absolute;
    right: 30px;
    top: 120px;
    text-align: left;
    color: var(--text-light);
    font-size: 13px;
    line-height: 1.35;
    width: 210px;
  }
  .contact__web { letter-spacing: 2px; font-size: 12px; margin-bottom: 22px; }
  .contact__address { margin-bottom: 12px; }
</style>
</head>
<body>
  <section class="card card--front" aria-label="Card front">
    <div class="brand-lockup">
      <div class="wordmark"><span class="wordmark__square"></span>FEN ATHLETICS</div>
      <div class="tagline">PERFORMANCE WEAR</div>
      <div class="rule"></div>
      <div class="brand-row">
        <div class="brand-badge"><span class="brand-badge__shape shape-purple"></span><span class="brand-badge__name">TavaPuni</span></div>
        <div class="brand-badge"><span class="brand-badge__shape shape-grey"></span><span class="brand-badge__name">ElmStretch</span></div>
        <div class="brand-badge"><span class="brand-badge__shape shape-pink"></span><span class="brand-badge__name">Grit and Rain</span></div>
        <div class="brand-badge"><span class="brand-badge__shape shape-light"></span><span class="brand-badge__name">Fen</span></div>
      </div>
    </div>
    <div class="edge-band"><span class="edge-band__red"></span><span class="edge-band__rest"></span></div>
  </section>

  <section class="card card--back" aria-label="Card back">
    <div class="brand-lockup">
      <div class="wordmark"><span class="wordmark__square"></span>FEN ATHLETICS</div>
      <div class="tagline">PERFORMANCE WEAR</div>
      <div class="brand-row">
        <div class="brand-badge"><span class="brand-badge__shape shape-purple"></span><span class="brand-badge__name">TavaPuni</span></div>
        <div class="brand-badge"><span class="brand-badge__shape shape-grey"></span><span class="brand-badge__name">ElmStretch</span></div>
        <div class="brand-badge"><span class="brand-badge__shape shape-pink"></span><span class="brand-badge__name">Grit and Rain</span></div>
        <div class="brand-badge"><span class="brand-badge__shape shape-light"></span><span class="brand-badge__name">Fen</span></div>
      </div>
      <div class="company-line">FEN ATHLETICS (LTD)</div>
    </div>
    <div class="person">
      <p class="person__name">Leo Pemberton-Hale</p>
      <p class="person__role">Operations Manager</p>
    </div>
    <div class="contact">
      <p class="contact__web">www.fenathletics.co.uk</p>
      <p class="contact__address">Ashby Yard, Kelmoor,<br>Dunholt, ZX4 2QP</p>
      <p>(+44) 1632 960 418</p>
      <p>Leo@fenathletics.co.uk</p>
    </div>
    <div class="edge-band"><span class="edge-band__red"></span><span class="edge-band__rest"></span></div>
  </section>
</body>
</html>
```